Lone Star Wetland Flora Stewardship Guild

We need to design the home page of this new website. We would like a fun website design for provides as a resource for members and information for potential members.
Please design so that we can see a portion of background on each side on the website.
I just need the final design files psd no coding needed.
Attached is their logo (colors are not 100% set in stone either so can mess with those as I did in the quick mockup attached)
Attached is a pdf newsletter they send out, you can get a feel for them and what they are about. The design is crappy and we are here to fix that going forward and we are starting with the website.
Here are some quick example websites (design style is open)
- I attached a quick mockup i did just for a content visual but by all means do what you want.
- http://www.brightpathleaders.example/
- http://www.civicunityhub.example/
- http://preview.webskinvault.example/show.php?cat=layouts&host=skinbazaar&temp=novaline
- http://www.meadowkeep.example/
- http://www.urbangleaners.example/
- http://www.projectcozyknit.example/
here are some of the other chapters website (pretty bad!)
and here are some of the others:
- http://www.dwrvcs.example/
- http://kwfg.example/
- http://www.blvcg.example/
Content Items that need to be included:
1. Logo
2. Menu - home, about, members, resources, events, membership, contact
3. Become a member - button or action
4. social links - chatterloop, workweave, clipstream
5. banner - that needs to explain their purpose "Promoting environmental stewardship through operations, research, education and outreach" (or this can be worked into the design)
6. Upcoming event (s)
7. Advertisement - members can place an ad on the website, this can be a placeholder for now
8. newsletter signup
9. advertise with us - this link can be in the footer
30-60 years of age, succesfull (household budgets of 120K+ men and women that live in texas.
Education

```html
<!DOCTYPE html>
<html lang="en">
<head>
<meta charset="utf-8">
<title>Lone Star Wetland Flora Stewardship Guild</title>
<link href="https://fonts.googleapis.com/css2?family=Signika:wght@400;600&family=Source+Sans+3:wght@400;600&display=swap" rel="stylesheet">
<style>
:root{
  --blue:#0d3f8a;
  --blue-dark:#0a3274;
  --red:#d94a56;
  --text:#555;
  --heading:#333;
  --nav-bg:#e4e4e4;
  --line:#d6d6d6;
  --olive:#857443;
  --footer:#3b3b3b;
  --footer-bottom:#323232;
  --footer-text:#b9b9b9;
  --white:#fff;
}
*{box-sizing:border-box;margin:0;padding:0}
html,body{width:1101px;height:1200px;overflow:hidden}
body{
  position:relative;
  font-family:"Source Sans 3",sans-serif;
  color:var(--text);
  background:linear-gradient(180deg,#5f86c4 0%,#a9c0dc 14%,#d7e1e8 22%,#8aa55a 30%,#6f8a3f 45%,#7d8a47 58%,var(--olive) 72%,var(--olive) 100%);
}
.page{position:absolute;left:106px;top:28px;width:889px;height:880px;background:var(--white);box-shadow:0 0 6px rgba(0,0,0,.15)}
.logo{position:absolute;left:16px;top:30px;display:flex;align-items:center;gap:8px}
.logo-mark{width:26px;height:26px;border-radius:50%;background:var(--red)}
.logo-name{font-family:"Signika",sans-serif;font-weight:600;font-size:30px;color:var(--blue);letter-spacing:1px}
.social-top{position:absolute;left:610px;top:22px;display:flex;gap:6px}
.social-top span{width:25px;height:25px;border-radius:50%;display:block}
.utility{position:absolute;left:757px;top:27px;font-size:13px;color:#666}
.utility span{margin:0 8px;color:#888}
.tagline{position:absolute;right:204px;top:81px;font-family:"Signika",sans-serif;font-size:15px;color:#333;letter-spacing:.3px;white-space:nowrap;text-align:right}
.btn{display:inline-block;font-family:"Signika",sans-serif;color:var(--white);text-align:center}
.btn-member{position:absolute;left:709px;top:66px;width:166px;height:38px;line-height:38px;background:var(--red);font-size:15px}
.nav{position:absolute;left:13px;top:120px;width:862px;height:47px;background:var(--nav-bg);display:flex;font-family:"Signika",sans-serif;font-size:13px;color:#444}
.nav a{display:block;line-height:47px;text-decoration:none;color:inherit;text-align:center}
.nav .active{color:var(--blue);border-bottom:5px solid var(--blue);height:47px;line-height:47px}
.banner{position:absolute;left:13px;top:181px;width:862px;height:324px;background:linear-gradient(180deg,#cfdde8 0%,#9ab27a 22%,#4f6a34 38%,#6b6f55 50%,#8f9c5a 70%,#7a7a4c 100%)}
.caption{position:absolute;left:48px;background:rgba(40,40,40,.55);color:var(--white);font-family:"Signika",sans-serif;font-size:22px;padding:0 14px;height:37px;line-height:37px;white-space:nowrap}
.btn-more{position:absolute;left:49px;top:201px;width:154px;height:41px;line-height:41px;background:var(--blue);font-size:15px}
.next{position:absolute;left:813px;top:160px}
.card{position:absolute;top:562px;height:285px;border:1px solid var(--line);background:var(--white)}
.card h2{font-family:"Signika",sans-serif;font-weight:400;font-size:22px;color:var(--blue)}
.about{left:16px;width:268px;padding:18px 14px}
.about h2{padding-bottom:4px;border-bottom:1px solid var(--line)}
.about p{margin-top:24px;font-size:12.5px;line-height:22px;color:#666}
.btn-read{position:absolute;right:16px;top:234px;width:100px;height:34px;line-height:34px;background:var(--red);font-size:13px}
.events{left:311px;width:268px;padding:18px 16px}
.arrows{position:absolute;right:16px;top:24px;display:flex;gap:3px}
.event{display:flex;gap:22px;margin-top:16px}
.event:first-of-type{margin-top:18px}
.thumb{width:76px;height:56px;border:1px solid var(--line);padding:5px;flex:none}
.thumb div{width:100%;height:100%}
.event p{font-size:12px;line-height:18px;color:#666}
.ad{position:absolute;left:608px;top:562px;width:267px;height:286px;overflow:hidden;background:linear-gradient(160deg,#7fd2e6 0%,#2aa8cc 55%,#1b7fa8 100%)}
.ad-name{position:absolute;left:40px;top:238px;font-family:"Signika",sans-serif;font-weight:600;font-size:20px;color:#333;white-space:nowrap}
.ad-url{position:absolute;left:30px;top:265px;font-size:11px;letter-spacing:4px;color:#333;white-space:nowrap}
.ad-badge{position:absolute;left:178px;top:212px;width:82px;height:72px;border-radius:50%;background:#f6a21c;color:var(--white);font-family:"Signika",sans-serif;font-size:12px;font-weight:600;text-align:center;padding-top:22px;line-height:14px}
.footer{position:absolute;left:0;top:945px;width:1101px;height:203px;background:var(--footer);color:var(--footer-text)}
.footer h3{font-family:"Signika",sans-serif;font-weight:400;font-size:15px;color:#ddd;letter-spacing:.5px}
.f-nav{position:absolute;left:123px;top:26px}
.f-nav ul{list-style:none;margin-top:12px;font-size:12.5px;line-height:21.5px}
.f-follow{position:absolute;left:353px;top:27px}
.f-follow ul{list-style:none;margin-top:12px;font-size:12.5px}
.f-follow li{display:flex;align-items:center;gap:16px;height:33px}
.f-follow i{width:22px;height:22px;border-radius:50%;background:#8a8a8a;display:block}
.map{position:absolute;left:528px;top:31px;width:202px;height:126px;background:linear-gradient(135deg,#e6e2d6 0%,#d8dccb 40%,#efd9a8 60%,#e2e4df 100%)}
.f-loc{position:absolute;left:762px;top:32px;font-size:12.5px;line-height:22px}
.f-loc h3{margin-bottom:10px}
.f-loc .gap{margin-top:10px}
.bottom{position:absolute;left:0;top:1148px;width:1101px;height:52px;background:var(--footer-bottom);color:#aaa;font-size:12.5px;text-align:center;line-height:52px}
</style>
</head>
<body>
<div class="page">
  <div class="logo"><span class="logo-mark"></span><span class="logo-name">LSWFSG</span></div>
  <div class="social-top" aria-label="Social links">
    <span style="background:#1f5fa8" aria-label="Chatterloop"></span>
    <span style="background:#2b8fd1" aria-label="Chirpline"></span>
    <span style="background:#f39a1e" aria-label="RSS"></span>
    <span style="background:#c8402f" aria-label="Orbitcircle"></span>
  </div>
  <div class="utility">Contact Us<span>|</span>Login</div>
  <div class="tagline">LONE STAR WETLAND FLORA STEWARDSHIP GUILD</div>
  <a class="btn btn-member">Become A Member</a>
  <nav class="nav">
    <a class="active" style="width:97px">HOME</a>
    <a style="width:122px">ABOUT</a>
    <a style="width:100px">MEMBERS</a>
    <a style="width:138px">RESOURCES</a>
    <a style="width:95px">EVENTS</a>
    <a style="width:145px">MEMBERSHIP</a>
    <a style="width:100px">CONTACT</a>
  </nav>
  <div class="banner" role="img" aria-label="Photo of a calm pond covered with lily pads, trees on the far bank">
    <div class="caption" style="top:93px">Promoting environmental stewardship through operations,</div>
    <div class="caption" style="top:148px">research, education and outreach</div>
    <a class="btn btn-more">Find Out More</a>
    <svg class="next" width="32" height="32" viewBox="0 0 32 32"><circle cx="16" cy="16" r="15" fill="#fff" stroke="#ccc"/><path d="M13 9l7 7-7 7" fill="none" stroke="#444" stroke-width="3"/></svg>
  </div>

  <section class="card about">
    <h2>About LSWFSG</h2>
    <p>Lorem ipsum dolor sit amet, consectetur adi pisicing elit, sed do eiusmod tempor incidiu nt ut labore et dolore magna aliqua. Ut enim ad minim veniam, quis nostrud exercitation ullamco laboris nisi ut aliquip ex ea commod consequat. Duis aute irure dolor in reprehen derit in voluptate velit.</p>
    <a class="btn btn-read">Read More</a>
  </section>

  <section class="card events">
    <h2>Upcoming Event</h2>
    <div class="arrows">
      <svg width="18" height="18" viewBox="0 0 18 18"><circle cx="9" cy="9" r="8" fill="none" stroke="#bbb"/><path d="M12 9H6M8 6L5 9l3 3" fill="none" stroke="#aaa" stroke-width="1.4"/></svg>
      <svg width="18" height="18" viewBox="0 0 18 18"><circle cx="9" cy="9" r="8" fill="none" stroke="#bbb"/><path d="M6 9h6M10 6l3 3-3 3" fill="none" stroke="#aaa" stroke-width="1.4"/></svg>
    </div>
    <div class="event"><div class="thumb"><div role="img" aria-label="Cedar Lodge venue emblem" style="background:#f1f1f1"></div></div><p>Excepteur sint occaecat cupidatat non proident, sunt in culpa.</p></div>
    <div class="event"><div class="thumb"><div role="img" aria-label="Lily pads on water" style="background:linear-gradient(135deg,#6a7a52,#b7c46a)"></div></div><p>Excepteur sint occaecat cupidatat non proident, sunt in culpa.</p></div>
    <div class="event"><div class="thumb"><div role="img" aria-label="River lined with trees" style="background:linear-gradient(180deg,#cfe0c0,#4f7a35)"></div></div><p>Excepteur sint occaecat cupidatat non proident, sunt in culpa.</p></div>
  </section>

  <div class="ad" role="img" aria-label="Advertisement placeholder: illustration of a handheld game console">
    <div class="ad-name">POCKETPLAY</div>
    <div class="ad-url">WWW.POCKETPLAY</div>
    <div class="ad-badge">CLICK FOR<br>FULLSIZE</div>
  </div>
</div>

<footer class="footer">
  <div class="f-nav">
    <h3>NAVIGATION LINK</h3>
    <ul><li>Home</li><li>Solutions</li><li>Services</li><li>Partners</li><li>Clients</li><li>About Us</li></ul>
  </div>
  <div class="f-follow">
    <h3>FOLLOW US</h3>
    <ul>
      <li><i></i>Chatterloop</li>
      <li><i></i>Chirpline</li>
      <li><i></i>Orbitcircle</li>
      <li><i></i>RSS</li>
    </ul>
  </div>
  <div class="map" role="img" aria-label="Street map showing the guild office location"></div>
  <div class="f-loc">
    <h3>LOCATION</h3>
    <div>222, Street Number, Buliding Number,</div>
    <div>Area Name, City Name, Zip Code.</div>
    <div class="gap">Call Us : 555 014 2288</div>
    <div>Email : info@wetlandguild.example</div>
  </div>
</footer>
<div class="bottom">©2014 Yoursite - Terms of Service - Privacy Policy</div>
</body>
</html>
```